SILVER LANTERN needs a Graphic Design (Women menstraul sanitary pads)

GRAPHIC DESIGN for the outside packiging and inside packaging.
Silver lantern company deals with women menstraul pads 3 different sizes and one 1 period underwear. It is a new company in Kenya.
3 different pads names should reflect on the outside
a) Overnight Maxi pad called Tundo. Heavy Absorbency.
b) Day pad called Seluna
c) Small called Pelito
All should have a symbol of a girl paint filled a)fully, b)half way and c)knee length filled.
1 period under wear called Vesta for overnight, Extra Heavy Absorbency.
All products should have (Mid-Bed infused with 100% plant -based choacoal to help stop Odour).
For the inside graphic design packaging kindly play around with the afro - colours of the mug i have provided so it can look authentic and also (think of Brazilian carnival colours).
The outside package which comprises of two different once (one made of nylon for the pads and the other one (period underwear)more of a box for should have 2 -3 colours at most, more warm girly colours for example mint & rose gold may be black too. One of the colours should be dominating.
The outside packaging of the period underwear comes in 3 different sizes S,M,L should all have a symbol of an under wear.
At the back should have;
DO NOT FLUSH this product, to dispose pad; wrap dispose with normal house hold waste.
Organic product, climate friendly. Smooth and High Quality
Designed & tested in Kenya, Made in China.
Family owned business

Target Market(s)

Female

Industry/Entity Type

Sanitary wear

Font styles to use
Decorative

Requirements
Must have
• Outside packaging Name of the company, logo, how many they are in a pack, their specific names and what time to be used.
Nice to have
• The packaging meant for the menstraul pantie which is the box like should have a symbol of an underwear, showing sizes (SML) and 8 for how many they are in that package. Over night pads 10 and all other pads 14. All pads shoul say Ultra Thin, With Wings, No Harsh Ingridients, No Leak, No Smells Odour-Controlling Charcoal

```html
<!DOCTYPE html>
<html lang="en">
<head>
<meta charset="utf-8">
<title>Silver Lantern – Pelito Small Pad Packaging</title>
<link rel="stylesheet" href="https://fonts.googleapis.com/css2?family=Lilita+One&family=Lora:ital@1&display=swap">
<style>
  :root {
    --page: #f4f4f4;
    --mint: #45b989;
    --blush: #efe1dc;
    --rose: #e2526d;
    --cream: #f6efeb;
    --white: #ffffff;
    --plum: #4b2a78;
    --ink: #1c1c1c;
    --pad: #e6e7ea;
    --pattern-a: #d13d7a;
    --pattern-b: #7a3fb0;
    --pattern-c: #f0873a;
    --pattern-d: #2d6fc0;
  }
  * { margin: 0; padding: 0; box-sizing: border-box; }
  html, body { width: 1200px; height: 799px; overflow: hidden; background: var(--page); }
  .stage { position: relative; width: 1200px; height: 799px; }

  .panel {
    position: absolute; top: 110px; width: 500px; height: 570px;
    overflow: hidden; box-shadow: 0 6px 24px rgba(0,0,0,.08);
  }
  .panel--front { left: 60px; background: var(--mint); }
  .panel--back { left: 640px; background: var(--mint); }
  .back-top { position: absolute; left: 0; top: 0; width: 100%; height: 300px; background: var(--blush); }

  .brand { position: absolute; left: 34px; top: 64px; }
  .brand__name { font-family: "Lilita One", sans-serif; font-size: 28px; line-height: 1; color: var(--white); }
  .brand__tag { font-family: "Lora", serif; font-style: italic; font-size: 10px; color: var(--white); margin-top: 5px; }
  .panel--back .brand__name, .panel--back .brand__tag { color: var(--rose); }

  .claims { position: absolute; right: 26px; top: 44px; display: flex; flex-direction: column; gap: 6px; }
  .claim {
    width: 104px; min-height: 28px; padding: 3px 7px; border: 1.5px solid var(--white); border-radius: 5px;
    font-family: "Lilita One", sans-serif; font-size: 11px; line-height: 1.1; color: var(--white); text-align: right;
    display: flex; align-items: center; justify-content: flex-end;
  }
  .panel--back .claim { border-color: var(--rose); color: var(--rose); }

  .pattern { position: absolute; }
  .product {
    position: absolute; text-align: center;
    font-family: "Lilita One", sans-serif; color: var(--cream); line-height: 1;
  }
  .product__size { display: block; }
  .product__name { display: block; }

  .pad-art, .figure-art { position: absolute; }

  .count {
    position: absolute; font-family: "Lilita One", sans-serif; color: var(--white);
    text-align: center; line-height: .95;
  }
  .count b { display: block; font-size: 24px; font-weight: 400; }
  .count span { font-size: 11px; }

  .copy { position: absolute; font-family: "Lilita One", sans-serif; color: var(--white); font-size: 13px; line-height: 1.25; }

  .seal {
    position: absolute; width: 78px; height: 78px; border-radius: 50%; background: var(--cream);
    border: 2px solid var(--rose); display: flex; flex-direction: column; align-items: center; justify-content: center;
    text-align: center; font-family: "Lilita One", sans-serif; color: var(--rose); font-size: 7.5px; line-height: 1.15; padding: 8px;
  }
  .icons { position: absolute; display: flex; gap: 8px; }
</style>
</head>
<body>
<main class="stage">

  <section class="panel panel--front">
    <div class="brand">
      <div class="brand__name">Silver Lantern</div>
      <div class="brand__tag">Gentle Care, Every Day</div>
    </div>
    <div class="claims">
      <div class="claim">Smooth and High Quality</div>
      <div class="claim">Organic Product</div>
      <div class="claim">Climate Friendly</div>
    </div>

    <svg class="pattern" style="left:0;top:180px" width="500" height="330" viewBox="0 0 500 330" role="img" aria-label="Colourful afro carnival pattern">
      <defs>
        <linearGradient id="patFront" x1="0" y1="0" x2="1" y2="1">
          <stop offset="0" stop-color="#7a3fb0"/>
          <stop offset=".35" stop-color="#d13d7a"/>
          <stop offset=".7" stop-color="#f0873a"/>
          <stop offset="1" stop-color="#2d6fc0"/>
        </linearGradient>
      </defs>
      <path d="M0 60 C60 10 160 0 260 20 C340 35 400 10 450 30 C500 50 500 130 480 190 C460 250 500 300 430 320 L0 330 Z" fill="url(#patFront)"/>
    </svg>

    <p class="product" style="left:90px;top:240px;width:240px">
      <span class="product__size" style="font-size:24px">Small Pad</span>
      <span class="product__name" style="font-size:60px">Pelito</span>
    </p>

    <svg class="pad-art" style="left:20px;top:370px" width="110" height="120" viewBox="0 0 110 120" role="img" aria-label="Sanitary pad with wings">
      <rect x="6" y="6" width="98" height="108" rx="38" fill="var(--pad)"/>
    </svg>

    <svg class="figure-art" style="left:350px;top:300px" width="90" height="200" viewBox="0 0 90 200" role="img" aria-label="Girl symbol filled to knee length">
      <rect x="10" y="0" width="70" height="200" rx="28" fill="var(--cream)"/>
    </svg>

    <svg style="position:absolute;left:108px;top:440px" width="90" height="50" viewBox="0 0 90 50" aria-hidden="true">
      <path d="M12 0 H90 L78 50 H0 Z" fill="var(--plum)"/>
    </svg>
    <div class="count" style="left:120px;top:447px;width:66px"><b>14</b><span>Pads</span></div>

    <p class="copy" style="left:26px;top:512px;width:300px">Mid-Bed infused with 100% plant-based charcoal to help stop Odor.</p>
  </section>

  <section class="panel panel--back">
    <div class="back-top"></div>
    <div class="brand">
      <div class="brand__name">Silver Lantern</div>
      <div class="brand__tag">Gentle Care, Every Day</div>
    </div>
    <div class="claims">
      <div class="claim">Smooth and High Quality</div>
      <div class="claim">Organic Product</div>
      <div class="claim">Climate Friendly</div>
    </div>

    <svg class="pattern" style="left:30px;top:150px" width="340" height="180" viewBox="0 0 340 180" role="img" aria-label="Colourful afro carnival pattern">
      <defs>
        <linearGradient id="patBack" x1="0" y1="0" x2="1" y2="1">
          <stop offset="0" stop-color="#f0873a"/>
          <stop offset=".4" stop-color="#d13d7a"/>
          <stop offset=".75" stop-color="#7a3fb0"/>
          <stop offset="1" stop-color="#2d6fc0"/>
        </linearGradient>
      </defs>
      <path d="M20 40 C80 0 260 0 320 30 C345 60 330 130 290 160 C230 185 90 180 40 150 C0 120 -5 60 20 40 Z" fill="url(#patBack)"/>
    </svg>

    <p class="product" style="left:95px;top:185px;width:210px">
      <span class="product__size" style="font-size:20px">Small Pad</span>
      <span class="product__name" style="font-size:50px">Pelito</span>
    </p>

    <div class="seal" style="left:396px;top:250px">
      <div>FAMILY OWNED BUSINESS</div>
      <div>Designed &amp; Tested in Kenya</div>
      <div>Made in China</div>
    </div>

    <svg class="pad-art" style="left:236px;top:312px" width="96" height="116" viewBox="0 0 96 116" role="img" aria-label="Sanitary pad with wings">
      <rect x="4" y="4" width="88" height="108" rx="36" fill="var(--pad)"/>
    </svg>

    <svg style="position:absolute;left:340px;top:360px" width="110" height="50" viewBox="0 0 110 50" aria-hidden="true">
      <rect x="0" y="0" width="110" height="50" rx="25" fill="var(--ink)"/>
    </svg>
    <div class="count" style="left:360px;top:366px;width:70px"><b>14</b><span>Pads</span></div>

    <div class="icons" style="left:30px;top:390px" aria-hidden="true">
      <svg width="30" height="30" viewBox="0 0 30 30">
        <circle cx="15" cy="15" r="13" fill="var(--white)" stroke="var(--rose)" stroke-width="2"/>
        <rect x="10" y="11" width="10" height="10" rx="2" fill="var(--ink)"/>
        <line x1="6" y1="6" x2="24" y2="24" stroke="var(--rose)" stroke-width="2"/>
      </svg>
      <svg width="30" height="30" viewBox="0 0 30 30">
        <circle cx="15" cy="15" r="13" fill="var(--white)"/>
        <path d="M10 11 H20 L18 23 H12 Z" fill="var(--ink)"/>
        <rect x="9" y="8" width="12" height="2" fill="var(--ink)"/>
      </svg>
    </div>

    <p class="copy" style="left:30px;top:430px;width:190px;font-size:11px">DO NOT FLUSH this product. To dispose of the pad, wrap and dispose with normal household waste</p>

    <p class="copy" style="left:236px;top:440px;width:240px">Ultra Thin, With Wings, No Harsh Ingredients, No Leak, No Smells Odor-Controlling Charcoal.</p>
  </section>

</main>
</body>
</html>
```